Business Cards - Brightpath Horizon

need to design unique business card for my mortgage business. I need to design credit card style business card for my business or any unique idea that you might have

Target Market(s)

Home Loan customers

Industry/Entity Type

Mortgage Brokerage

Contact Information for Business Card

please design credit card style or very unique style business card

Colors

Designer to choose colors to be used in the design.

Requirements
Must have
• Name
• position
• Phone number
• fax number
• email address
• website address
• social media address
• All above fields will be provided once design in finalised

```html
<!DOCTYPE html>
<html lang="en">
<head>
<meta charset="utf-8">
<title>Brightpath Horizon – Business Card</title>
<link rel="stylesheet" href="https://fonts.googleapis.com/css2?family=Libre+Baskerville&family=Share+Tech+Mono&display=swap">
<style>
  :root {
    --page-bg: #d9d2c8;
    --card-deep: #0a2270;
    --card-mid: #1747a8;
    --text-light: #d6def5;
    --text-soft: #b9c6ea;
    --number: #eef3ff;
    --rule: #9fb3e4;
    --social: #c7b3a8;
  }
  * { margin: 0; padding: 0; box-sizing: border-box; }
  html, body {
    width: 1200px;
    height: 969px;
    overflow: hidden;
    background: var(--page-bg);
  }
  .card {
    position: absolute;
    left: 100px;
    top: 200px;
    width: 1000px;
    height: 570px;
    border-radius: 34px;
    overflow: hidden;
    background:
      radial-gradient(ellipse 55% 65% at 30% 30%, rgba(79,139,224,0.75), rgba(79,139,224,0) 70%),
      linear-gradient(120deg, var(--card-mid) 0%, #123c98 45%, var(--card-deep) 100%);
    font-family: "Libre Baskerville", "Times New Roman", serif;
    color: var(--text-light);
  }
  .tree-backdrop {
    position: absolute;
    left: 0;
    top: 0;
    width: 506px;
    height: 570px;
    background: radial-gradient(ellipse 70% 60% at 45% 40%, rgba(150,190,240,0.22), rgba(150,190,240,0) 75%);
  }
  .holder-name {
    position: absolute;
    left: 62px;
    top: 66px;
    font-size: 32px;
    letter-spacing: 1px;
  }
  .holder-role {
    position: absolute;
    left: 62px;
    top: 118px;
    font-size: 21px;
    color: var(--text-soft);
  }
  .header-rule {
    position: absolute;
    left: 285px;
    top: 142px;
    width: 648px;
    height: 2px;
    background: var(--rule);
    opacity: 0.8;
  }
  .brand-top {
    position: absolute;
    right: 68px;
    top: 84px;
    font-size: 26px;
    color: var(--text-light);
    display: flex;
    align-items: center;
    gap: 12px;
    white-space: nowrap;
  }
  .brand-top .mark {
    width: 22px;
    height: 22px;
    background: var(--text-light);
  }
  .website {
    position: absolute;
    right: 90px;
    top: 158px;
    font-size: 20px;
    color: var(--text-soft);
  }
  .card-number {
    position: absolute;
    left: 222px;
    top: 238px;
    font-family: "Share Tech Mono", monospace;
    font-size: 76px;
    letter-spacing: 6px;
    color: var(--number);
    white-space: nowrap;
  }
  .address, .contact {
    position: absolute;
    left: 62px;
    font-size: 21px;
    line-height: 33px;
    color: var(--text-light);
    white-space: nowrap;
  }
  .address { top: 385px; }
  .contact { top: 460px; }
  .social {
    position: absolute;
    left: 421px;
    top: 478px;
    display: flex;
    gap: 6px;
  }
  .social span {
    width: 42px;
    height: 42px;
    border-radius: 50%;
    background: var(--social);
    opacity: 0.85;
  }
  .brand-main {
    position: absolute;
    left: 640px;
    top: 400px;
    width: 320px;
    text-align: center;
    color: var(--text-light);
  }
  .brand-main .name {
    font-size: 34px;
    line-height: 44px;
  }
  .brand-main .tagline {
    margin-top: 8px;
    font-size: 17px;
    color: var(--text-soft);
    white-space: nowrap;
  }
</style>
</head>
<body>
  <section class="card">
    <div class="tree-backdrop" role="img" aria-label="Faint illustration of a tree in the card background"></div>

    <div class="holder-name">DANIEL REYES</div>
    <div class="holder-role">CEO/FOUNDER</div>
    <div class="header-rule"></div>

    <div class="brand-top"><span class="mark"></span>Brightpath Horizon</div>
    <div class="website">www.bphorizon.com</div>

    <div class="card-number">907 555 0172</div>

    <div class="address">2140 Alder Ridge Road<br>Fairbanks, Alaska 99701</div>
    <div class="contact">P: 907 555 0148<br>E: info@bphorizon.com</div>

    <div class="social" aria-label="Social media links">
      <span></span><span></span><span></span><span></span>
    </div>

    <div class="brand-main">
      <div class="name">Brightpath<br>Horizon</div>
      <div class="tagline">Clear terms, Steady steps</div>
    </div>
  </section>
</body>
</html>
```